IT Services Company Needs Corporate PPT Template

This is urgent (need a fast turn around). We need a corporate PPT template deck (NOTE: Deck should be in 4:3 ratio) for our IT Services firm that is clean but slick and modern. We tend to lean more towards the flat design look. I'm attaching a zip file which includes our Corporate Branding Guide (which is in progress), color scheme, A PPT deck as inspiration (our logo is on the last slide), our font (LATO). Our newly launched website is located at: http://www.veranthix.com.

As an example of a deck we like see: http://slidemorrow.net/item/clean-multipurpose-business-presentation-template/5318206?WT.ac=category_thumb&WT.seg_1=category_thumb&WT.z_author=PixelHarbor
Although we don't want "this" deck - it gives an idea of style.

I'm also attaching a copy of our corporate deck as it is now to give you an idea of the type of content that would appear on various slides. We definitely want the following slides (at least) within the template:

Title Slide
Blank Slide
2 Column - with bullets
2 Column - no bullets
Single Column - no bullets
Single Column - with bullets
Various Charts and Tables (see example deck)
Meet the Team
Offering Slide
Customer Showcase
Timeline
Case Study
Contact US

Note: Being awarded this job will lead to a second job of creating our corporate deck.

Target Market(s)

CIO, CEO, Technology Officers, Sales People, Marketing, IT heads and staff, Customers, Prospective customers

Industry/Entity Type

Business

Requirements
Must have
• See description and attached files

```html
<!DOCTYPE html>
<html lang="en">
<head>
<meta charset="utf-8">
<title>Veranthix Corporate Presentation Template</title>
<link href="https://fonts.googleapis.com/css2?family=Lato:wght@400;700;900&display=swap" rel="stylesheet">
<style>
:root{
  --page:#000;
  --navy:#0f5f87;
  --navy-deep:#0b4d70;
  --band:#106b98;
  --accent:#2a8cc4;
  --text:#555;
  --dark:#333;
  --paper:#fff;
  --mist:#eef2f5;
  --line:#d9dee3;
  --bar-blue:#4a7fc1;
  --bar-green:#8db94a;
  --bar-cyan:#4fb3d1;
  --pie-navy:#1b4f7a;
  --pie-cyan:#5bbcd8;
  --pie-dark:#4a4a4a;
  --pie-grey:#7a7a7a;
}
*{box-sizing:border-box;margin:0;padding:0}
html,body{width:1177px;height:1200px;overflow:hidden;background:var(--page);font-family:'Lato',sans-serif}
.deck{position:absolute;left:21px;top:29px;display:grid;grid-template-columns:repeat(3,369px);grid-auto-rows:276px;column-gap:14px;row-gap:15px}
.slide{position:relative;overflow:hidden;background:linear-gradient(#fff 60%,var(--mist));color:var(--text)}
.slide.cover{background:linear-gradient(135deg,#11688f,var(--navy-deep))}
.hd{position:absolute;left:0;top:0;width:100%;height:27px;background:var(--navy);color:#fff;font-weight:700;font-size:12.5px;line-height:27px;padding-left:9px}
.hd.notch::after{content:"";position:absolute;left:16px;bottom:-6px;border:6px solid transparent;border-bottom:0;border-top-color:var(--navy)}
.ft{position:absolute;left:0;bottom:0;width:100%;height:17px;background:var(--band);display:flex;align-items:center;padding:0 7px}
.ft.light{background:#eceff2;height:22px}
.brand{font-weight:900;font-size:11px;color:#fff;letter-spacing:.2px}
.ft.light .brand{color:var(--navy);font-size:12px}
.connect{margin-left:auto;display:flex;align-items:center;gap:2px;font-size:4.5px;color:#fff;font-weight:700}
.connect span{margin-right:3px}
.connect i{display:block;width:7px;height:7px;background:#fff;opacity:.9}
.presenter{margin-left:auto;font-size:5.5px;color:var(--accent)}
.presenter b{font-size:7px;color:var(--accent)}
.sub{position:absolute;color:var(--accent);font-weight:700;font-size:9.5px}
.big-sub{font-size:12.5px}
.para{position:absolute;font-size:6.2px;line-height:1.65;color:var(--text)}
.para p+p{margin-top:7px}
.bullets{position:absolute;list-style:none;font-size:6.6px;color:var(--dark)}
.bullets li{position:relative;padding-left:12px}
.bullets li::before{content:"";position:absolute;left:0;top:0;width:8px;height:8px;background:var(--navy)}
.bullets li::after{content:"";position:absolute;left:1.6px;top:2.4px;width:2.6px;height:2.6px;border:solid #fff;border-width:1px 1px 0 0;transform:rotate(45deg)}
.wide li{font-size:7.4px;padding-left:14px}
.wide li::before{width:9px;height:9px}
.cover-logo{position:absolute;color:#fff;font-weight:900}
.tagline{position:absolute;left:166px;top:110px;width:200px;height:60px;background:#1571a1;border-left:3px solid #3d97c9;padding:6px 7px;color:#fff}
.tagline .t1{font-size:8px;font-weight:700}
.tagline .t2{font-size:13px;color:#cfe9f7}
.tagline .t3{font-size:5.5px;line-height:1.5;margin-top:3px}
.cards{position:absolute;left:14px;top:118px;display:grid;grid-template-columns:repeat(4,81px);gap:6px}
.card{height:115px;border:1px solid var(--line);background:#f7f8f9}
.card h4{background:var(--navy);color:#fff;font-size:6.8px;text-align:center;height:15px;line-height:15px}
.card p{font-size:5.6px;line-height:1.55;text-align:center;padding:6px 7px}
.table-box{position:absolute;left:20px;top:95px;width:329px;border:1px solid var(--line);padding:5px;background:#fff}
.table-box table{width:100%;border-collapse:separate;border-spacing:0 5px;font-size:5.9px}
.table-box th{background:var(--navy);color:#fff;text-align:left;font-size:7px;height:18px;padding-left:7px}
.table-box td{background:#e9eaeb;height:17px;padding-left:7px;color:var(--dark);font-weight:700}
.agenda{position:absolute;list-style:none}
.agenda li{display:flex;align-items:center;height:21px;width:150px;margin-bottom:11px;background:linear-gradient(90deg,#f2f4f6,rgba(242,244,246,0));font-size:8px;color:var(--dark)}
.agenda b{display:block;width:19px;height:19px;background:var(--accent);color:#fff;font-size:10px;line-height:19px;text-align:center;margin:0 10px 0 2px;border-left:3px solid #d9a441}
.team{position:absolute;left:20px;top:62px;display:grid;grid-template-columns:repeat(4,70px);column-gap:14px}
.member{text-align:center}
.photo{width:58px;height:58px;border-radius:50%;margin:0 auto;background:radial-gradient(circle at 50% 40%,#9aa7b4,#3c5a73);border:2px solid #1a5b82}
.role{position:relative;margin:8px auto 0;width:66px;background:var(--navy);color:#fff;padding:2px 0}
.role::before{content:"";position:absolute;left:29px;top:-5px;border:4px solid transparent;border-top:0;border-bottom:5px solid var(--navy)}
.role strong{display:block;font-size:6.8px}
.role span{font-size:5px}
.bio{font-size:5.2px;line-height:1.5;margin-top:4px;color:var(--text)}
svg text{font-family:'Lato',sans-serif}
</style>
</head>
<body>
<main class="deck">

  <section class="slide cover">
    <div class="cover-logo" style="left:28px;top:120px;font-size:24px">Veranthix</div>
    <div class="cover-logo" style="left:62px;top:153px;font-size:7.5px;font-weight:400">Name here</div>
    <div class="tagline">
      <div class="t1">The Art of Making the</div>
      <div class="t2">Impossible Possible</div>
      <div class="t3">Lorem ipsum dolor sit ipsum Lorem ipsum dolor sit ipsum<br>Lorem ipsum dolor sit ipsum</div>
    </div>
    <div style="position:absolute;left:7px;bottom:4px;font-size:5px;color:#8fc0dc">Copyright text here</div>
  </section>

  <section class="slide cover">
    <div class="cover-logo" style="left:218px;top:128px;font-size:23px">Veranthix</div>
    <div class="cover-logo" style="left:186px;top:162px;font-size:15px;font-weight:400">PROJECT TITLE HERE</div>
    <div style="position:absolute;right:26px;top:191px;width:190px;text-align:right;font-size:5.8px;line-height:1.55;color:#fff">Sub text here Sub text here Sub text here Sub text here Sub text here Sub text here Sub text here Sub text here</div>
  </section>

  <section class="slide">
    <div class="hd notch">Project Title Here</div>
    <div class="sub big-sub" style="left:19px;top:57px">Project Title Here</div>
    <div class="sub big-sub" style="left:200px;top:57px">Project Title Here</div>
    <div class="para" style="left:19px;top:79px;width:150px"><p>Lorem ipsum dolor sit ipsum Lorem ipsum dolor sit ipsum Lorem ipsum dolor sit ipsum ipsum dolor sit ipsum Lorem ipsum dolor sit ipsum Lorem ipsum dolor sit ipsum Lorem ipsum dolor sit ipsum Lorem ipsum dolor sit ipsum dolor sit ipsum</p><p>Lorem ipsum dolor sit ipsum Lorem ipsum dolor sit ipsum Lorem ipsum dolor sit ipsum ipsum dolor sit ipsum Lorem ipsum dolor sit ipsum Lorem ipsum dolor sit ipsum Lorem ipsum dolor sit ipsum Lorem ipsum dolor sit ipsum dolor sit ipsum Lorem ipsum dolor sit ipsum dolor sit ipsum</p></div>
    <div class="para" style="left:200px;top:79px;width:150px"><p>Lorem ipsum dolor sit ipsum Lorem ipsum dolor sit ipsum Lorem ipsum dolor sit ipsum ipsum dolor sit ipsum Lorem ipsum dolor sit ipsum Lorem ipsum dolor sit ipsum Lorem ipsum dolor sit ipsum Lorem ipsum dolor sit ipsum dolor sit ipsum</p><p>Lorem ipsum dolor sit ipsum Lorem ipsum dolor sit ipsum Lorem ipsum dolor sit ipsum ipsum dolor sit ipsum Lorem ipsum dolor sit ipsum Lorem ipsum dolor sit ipsum Lorem ipsum dolor sit ipsum Lorem ipsum dolor sit ipsum dolor sit ipsum Lorem ipsum dolor sit ipsum dolor sit ipsum</p></div>
    <footer class="ft"><span class="brand">Veranthix</span><div class="connect"><span>CONNECT WITH US:</span><i></i><i></i><i></i><i></i><i></i></div></footer>
  </section>

  <section class="slide">
    <div class="hd notch">Project Title Here</div>
    <div class="sub" style="left:19px;top:49px">Subtitle text here</div>
    <div class="sub" style="left:186px;top:49px">Subtitle text here</div>
    <ul class="bullets" style="left:19px;top:72px;line-height:8px"><li style="margin-bottom:11px">Lorem ipsum dolor sit ipsum Lorem dolor</li><li style="margin-bottom:11px">Lorem ipsum dolor sit ipsum Lorem dolor</li><li style="margin-bottom:11px">Lorem ipsum dolor sit ipsum Lorem dolor</li><li style="margin-bottom:11px">Lorem ipsum dolor sit ipsum Lorem dolor</li><li style="margin-bottom:11px">Lorem ipsum dolor sit ipsum Lorem dolor</li><li>Lorem ipsum dolor sit ipsum Lorem dolor</li></ul>
    <ul class="bullets" style="left:186px;top:72px;line-height:8px"><li style="margin-bottom:11px">Lorem ipsum dolor sit ipsum Lorem dolor</li><li style="margin-bottom:11px">Lorem ipsum dolor sit ipsum Lorem dolor</li><li style="margin-bottom:11px">Lorem ipsum dolor sit ipsum Lorem dolor</li><li style="margin-bottom:11px">Lorem ipsum dolor sit ipsum Lorem dolor</li><li style="margin-bottom:11px">Lorem ipsum dolor sit ipsum Lorem dolor</li><li>Lorem ipsum dolor sit ipsum Lorem dolor</li></ul>
    <footer class="ft"><span class="brand">Veranthix</span><div class="connect"><span>CONNECT WITH US:</span><i></i><i></i><i></i><i></i><i></i></div></footer>
  </section>

  <section class="slide">
    <div class="hd notch">Project Title Here</div>
    <div class="sub" style="left:19px;top:48px">Subtitle text here</div>
    <div class="para" style="left:19px;top:61px;width:336px"><p>Lorem ipsum dolor sit ipsum Lorem ipsum dolor sit ipsum Lorem ipsum dolor sit ipsum Lorem ipsum dolor sit ipsum Lorem ipsum dolor sit ipsum Lorem ipsum dolor sit ipsum Lorem ipsum dolor sit ipsum Lorem ipsum dolor sit ipsum Lorem ipsum dolor sit ipsum Lorem ipsum dolor sit ipsum Lorem ipsum dolor sit ipsum</p><p>Lorem ipsum dolor sit ipsum Lorem ipsum dolor sit ipsum Lorem ipsum dolor sit ipsum Lorem ipsum dolor sit ipsum Lorem ipsum dolor sit ipsum Lorem ipsum dolor sit ipsum Lorem ipsum dolor sit ipsum Lorem ipsum dolor sit ipsum Lorem ipsum dolor sit ipsum Lorem ipsum dolor sit ipsum</p></div>
    <div class="sub" style="left:19px;top:150px">Subtitle text here</div>
    <div class="para" style="left:19px;top:163px;width:336px"><p>Lorem ipsum dolor sit ipsum Lorem ipsum dolor sit ipsum Lorem ipsum dolor sit ipsum Lorem ipsum dolor sit ipsum Lorem ipsum dolor sit ipsum Lorem ipsum dolor sit ipsum Lorem ipsum dolor sit ipsum Lorem ipsum dolor sit ipsum Lorem ipsum dolor sit ipsum Lorem ipsum dolor sit ipsum Lorem ipsum dolor sit ipsum</p><p>Lorem ipsum dolor sit ipsum Lorem ipsum dolor sit ipsum Lorem ipsum dolor sit ipsum Lorem ipsum dolor sit ipsum Lorem ipsum dolor sit ipsum Lorem ipsum dolor sit ipsum Lorem ipsum dolor sit ipsum Lorem ipsum dolor sit ipsum Lorem ipsum dolor sit ipsum Lorem ipsum dolor sit ipsum</p></div>
    <footer class="ft"><span class="brand">Veranthix</span><div class="connect"><span>CONNECT WITH US:</span><i></i><i></i><i></i><i></i><i></i></div></footer>
  </section>

  <section class="slide">
    <div class="hd notch">Project Title Here</div>
    <div class="sub" style="left:19px;top:51px">Subtitle text here</div>
    <ul class="bullets wide" style="left:19px;top:76px;line-height:9px"><li style="margin-bottom:15px">Lorem ipsum dolor sit ipsum Lorem ipsuma dolor sit ipsum</li><li style="margin-bottom:15px">Lorem ipsum dolor sit ipsum Lorem ipsuma dolor sit ipsum</li><li style="margin-bottom:15px">Lorem ipsum dolor sit ipsum Lorem ipsuma dolor sit ipsum</li><li style="margin-bottom:15px">Lorem ipsum dolor sit ipsum Lorem ipsuma dolor sit ipsum</li><li style="margin-bottom:15px">Lorem ipsum dolor sit ipsum Lorem ipsuma dolor sit ipsum</li><li>Lorem ipsum dolor sit ipsum Lorem ipsuma dolor sit ipsum</li></ul>
    <footer class="ft"><span class="brand">Veranthix</span><div class="connect"><span>CONNECT WITH US:</span><i></i><i></i><i></i><i></i><i></i></div></footer>
  </section>

  <section class="slide">
    <div class="hd notch">Project Title Here</div>
    <div class="sub" style="left:19px;top:46px">Subtitle text here</div>
    <div class="para" style="left:19px;top:60px;width:336px">Lorem ipsum dolor sit ipsum Lorem dolor Lorem ipsum dolor sit ipsum Lorem dolor Lorem ipsum dolor sit ipsum Lorem ipsum dolor sit ipsum Lorem ipsum dolor Lorem ipsum dolor sit ipsum Lorem dolor Lorem ipsum dolor sit ipsum Lorem dolor Lorem ipsum dolor sit ipsum Lorem ipsum dolor Lorem ipsum dolor sit ipsum Lorem dolor Lorem ipsum dolor sit ipsum Lorem ipsum dolor sit ipsum Lorem dolor</div>
    <div class="cards">
      <div class="card"><h4>Title Here</h4><p>Lorem ipsum dolor sit ipsum Lorem dolor ipsum dolor sit ipsum Lorem dolor Lorem ipsum dolor sit ipsum Lorem dolor Lorem ipsum dolor sit ipsum Lorem dolor sit ipsum Lorem dolor</p></div>
      <div class="card"><h4>Title Here</h4><p>Lorem ipsum dolor sit ipsum Lorem dolor ipsum dolor sit ipsum Lorem dolor Lorem ipsum dolor sit ipsum Lorem dolor Lorem ipsum dolor sit ipsum Lorem dolor sit ipsum Lorem dolor</p></div>
      <div class="card"><h4>Title Here</h4><p>Lorem ipsum dolor sit ipsum Lorem dolor ipsum dolor sit ipsum Lorem dolor Lorem ipsum dolor sit ipsum Lorem dolor Lorem ipsum dolor sit ipsum Lorem dolor sit ipsum Lorem dolor</p></div>
      <div class="card"><h4>Title Here</h4><p>Lorem ipsum dolor sit ipsum Lorem dolor ipsum dolor sit ipsum Lorem dolor Lorem ipsum dolor sit ipsum Lorem dolor Lorem ipsum dolor sit ipsum Lorem dolor sit ipsum Lorem dolor</p></div>
    </div>
    <footer class="ft"><span class="brand">Veranthix</span><div class="connect"><span>CONNECT WITH US:</span><i></i><i></i><i></i><i></i><i></i></div></footer>
  </section>

  <section class="slide">
    <div class="hd notch">Project Title Here</div>
    <div class="para" style="left:22px;top:62px;width:330px">Lorem ipsum dolor sit ipsum Lorem ipsum dolor sit ipsum Lorem ipsum Lorem ipsum dolor sit ipsum Lorem ipsum dolor sit ipsum Lorem ipsum dolor sit ipsum</div>
    <div class="table-box">
      <table>
        <tr><th>Content Title Here</th><th>Content Title Here</th><th>Content Title Here</th></tr>
        <tr><td>Lorem ipsum dolor Lorem ipsum</td><td>Lorem ipsum dolor Lorem ipsum</td><td>Lorem ipsum dolor Lorem ipsum</td></tr>
        <tr><td>Lorem ipsum dolor Lorem ipsum</td><td>Lorem ipsum dolor Lorem ipsum</td><td>Lorem ipsum dolor Lorem ipsum</td></tr>
        <tr><td>Lorem ipsum dolor Lorem ipsum</td><td>Lorem ipsum dolor Lorem ipsum</td><td>Lorem ipsum dolor Lorem ipsum</td></tr>
        <tr><td>Lorem ipsum dolor Lorem ipsum</td><td>Lorem ipsum dolor Lorem ipsum</td><td>Lorem ipsum dolor Lorem ipsum</td></tr>
      </table>
    </div>
    <footer class="ft"><span class="brand">Veranthix</span><div class="connect"><span>CONNECT WITH US:</span><i></i><i></i><i></i><i></i><i></i></div></footer>
  </section>

  <section class="slide">
    <div class="hd" style="height:30px;line-height:30px">Sample Pie Chart</div>
    <div class="sub big-sub" style="left:22px;top:74px">Lorem ipsum dolor sit ipsum</div>
    <div class="para" style="left:22px;top:93px;width:168px"><p>Lorem ipsum dolor sit ipsum Lorem ipsum dolor sit ipsum Lorem ipsum dolor sit ipsum Lorem ipsum dolor sit ipsum Lorem ipsum dolor sit ipsum Lorem ipsum dolor sit ipsum Lorem ipsum dolor sit ipsum</p><p>Lorem ipsum dolor sit ipsum Lorem ipsum dolor sit ipsum Lorem ipsum dolor sit ipsum Lorem ipsum dolor sit ipsum Lorem ipsum dolor sit ipsum Lorem ipsum dolor sit ipsum Lorem ipsum dolor sit ipsum</p></div>
    <svg style="position:absolute;left:208px;top:72px" width="146" height="146" viewBox="-73 -73 146 146">
      <g stroke="#fff" stroke-width="1">
        <path d="M0 0L0 -70A70 70 0 0 1 40.2 -57.3Z" fill="var(--bar-blue)"/>
        <path d="M0 0L40.2 -57.3A70 70 0 0 1 65.8 23.9Z" fill="var(--pie-navy)"/>
        <path d="M0 0L65.8 23.9A70 70 0 0 1 23.9 65.8Z" fill="var(--bar-green)"/>
        <path d="M0 0L23.9 65.8A70 70 0 0 1 -65.8 23.9Z" fill="var(--pie-cyan)"/>
        <path d="M0 0L-65.8 23.9A70 70 0 0 1 -45 -53.6Z" fill="var(--pie-dark)"/>
        <path d="M0 0L-45 -53.6A70 70 0 0 1 0 -70Z" fill="var(--pie-grey)"/>
      </g>
      <g fill="#fff" font-size="5" text-anchor="middle">
        <text x="11" y="-50">Lorem</text><text x="11" y="-44">ipsum</text>
        <text x="-14" y="-50">Lorem</text><text x="-14" y="-44">ipsum</text><text x="-14" y="-38">dolor</text>
        <text x="40" y="-4">.Lorem ipsum</text><text x="40" y="2">dolor</text>
        <text x="33" y="31">.orem ipsum</text><text x="33" y="37">dolor</text>
        <text x="-5" y="36">Lorem ipsum dolor</text><text x="-5" y="42">Lorem ipsum dolor</text>
        <text x="-42" y="-9">.orem ipsum dolor</text><text x="-42" y="-3">.orem ipsum dolor</text>
      </g>
      <circle r="11" fill="#fff" stroke="var(--pie-navy)" stroke-width="2"/>
      <circle r="5" fill="var(--pie-navy)"/>
    </svg>
    <footer class="ft light"><span class="brand">Veranthix</span><span class="presenter">Presentator Name : <b>Lena Marosh</b></span></footer>
  </section>

  <section class="slide">
    <div class="hd notch">Project Title Here</div>
    <div class="sub" style="left:19px;top:71px">Subtitle text here</div>
    <div class="para" style="left:19px;top:85px;width:110px"><p>Lorem ipsum dolor sit ipsum Lorem dolor Lorem ipsum dolor sit ipsum Lorem ipsum dolor Lorem ipsum dolor Lorem ipsum dolor sit ipsum</p><p>Lorem dolorLorem ipsum dolor sit ipsum Lorem ipsum dolor sit ipsum Lorem dolor Lorem ipsum dolor sit ipsum</p></div>
    <svg style="position:absolute;left:140px;top:72px" width="225" height="140" viewBox="0 0 225 140" aria-label="Bar chart of three series across four categories">
      <g stroke="#d5d8db" stroke-width=".6">
        <line x1="18" y1="6" x2="222" y2="6"/><line x1="18" y1="24.5" x2="222" y2="24.5"/><line x1="18" y1="43" x2="222" y2="43"/><line x1="18" y1="61.5" x2="222" y2="61.5"/><line x1="18" y1="80" x2="222" y2="80"/><line x1="18" y1="98.5" x2="222" y2="98.5"/>
      </g>
      <line x1="18" y1="117" x2="222" y2="117" stroke="#555" stroke-width=".8"/>
      <g font-size="7" fill="#333" text-anchor="end"><text x="12" y="119">0</text><text x="12" y="100">1</text><text x="12" y="82">2</text><text x="12" y="63">3</text><text x="12" y="45">4</text><text x="12" y="26">5</text><text x="12" y="8">6</text></g>
      <g fill="var(--bar-blue)"><rect x="23" y="37.4" width="11" height="79.6"/><rect x="74" y="70.7" width="11" height="46.3"/><rect x="125" y="52.2" width="11" height="64.8"/><rect x="176" y="33.7" width="11" height="83.3"/></g>
      <g fill="var(--bar-green)"><rect x="35" y="72.6" width="11" height="44.4"/><rect x="86" y="35.6" width="11" height="81.4"/><rect x="137" y="83.7" width="11" height="33.3"/><rect x="188" y="65.2" width="11" height="51.8"/></g>
      <g fill="var(--bar-cyan)"><rect x="47" y="80" width="11" height="37"/><rect x="98" y="80" width="11" height="37"/><rect x="149" y="61.5" width="11" height="55.5"/><rect x="200" y="24.5" width="11" height="92.5"/></g>
      <g font-size="7" font-weight="700" fill="#333" text-anchor="middle"><text x="41" y="130">Category 1</text><text x="92" y="130">Category 2</text><text x="143" y="130">Category 3</text><text x="194" y="130">Category 4</text></g>
    </svg>
    <footer class="ft"><span class="brand">Veranthix</span><div class="connect"><span>CONNECT WITH US:</span><i></i><i></i><i></i><i></i><i></i></div></footer>
  </section>

  <section class="slide">
    <div class="hd">Project Title here</div>
    <div class="sub" style="left:10px;top:45px">Agenda Slide</div>
    <ol class="agenda" style="left:22px;top:73px"><li><b>01</b>Slide Title Here</li><li><b>02</b>Slide Title Here</li><li><b>03</b>Slide Title Here</li><li><b>04</b>Slide Title Here</li><li><b>05</b>Slide Title Here</li></ol>
    <ol class="agenda" style="left:187px;top:73px"><li><b>06</b>Slide Title Here</li><li><b>07</b>Slide Title Here</li><li><b>08</b>Slide Title Here</li><li><b>09</b>Slide Title Here</li><li><b>10</b>Slide Title Here</li></ol>
    <footer class="ft light"><span class="brand">Veranthix</span><span class="presenter">Presentator Name : <b>Lena Marosh</b></span></footer>
  </section>

  <section class="slide">
    <div class="hd">Meet the Team</div>
    <div class="sub" style="left:10px;top:42px;font-size:8.5px">Team Slide text here</div>
    <div class="team">
      <div class="member"><div class="photo" role="img" aria-label="Team member portrait"></div><div class="role"><strong>Tom Rellis</strong><span>Solution Director</span></div><p class="bio">consectetur adipiscing elit. Cras ipsum leo, ves-tibulum non orci id, vehicula convallis sem consectetur adipiscing elit. Cras ipsum leo, ves-tibulum non orci id, vehicula convallis sem</p></div>
      <div class="member"><div class="photo" role="img" aria-label="Team member portrait"></div><div class="role"><strong>Tom Rellis</strong><span>Solution Director</span></div><p class="bio">consectetur adipiscing elit. Cras ipsum leo, ves-tibulum non orci id, vehicula convallis sem consectetur adipiscing elit. Cras ipsum leo, ves-tibulum non orci id, vehicula convallis sem</p></div>
      <div class="member"><div class="photo" role="img" aria-label="Team member portrait"></div><div class="role"><strong>Tom Rellis</strong><span>Solution Director</span></div><p class="bio">consectetur adipiscing elit. Cras ipsum leo, ves-tibulum non orci id, vehicula convallis sem consectetur adipiscing elit. Cras ipsum leo, ves-tibulum non orci id, vehicula convallis sem</p></div>
      <div class="member"><div class="photo" role="img" aria-label="Team member portrait"></div><div class="role"><strong>Tom Rellis</strong><span>Solution Director</span></div><p class="bio">consectetur adipiscing elit. Cras ipsum leo, ves-tibulum non orci id, vehicula convallis sem consectetur adipiscing elit. Cras ipsum leo, ves-tibulum non orci id, vehicula convallis sem</p></div>
    </div>
    <footer class="ft light"><span class="brand">Veranthix</span><span class="presenter">Presentator Name : <b>Lena Marosh</b></span></footer>
  </section>

</main>
</body>
</html>
```